Moravel Aesthetic Doctor

I require an elegant, luxurious looking business card for my aesthetic business. I am a doctor and that will set me aside from competitors. I am planning to provide home and spa based treatments to clients with high expectations. I have attached my logo.

```html
<!DOCTYPE html>
<html lang="en">
<head>
<meta charset="utf-8">
<title>Moravel Aesthetic Doctor – Business Card</title>
<link rel="stylesheet" href="https://fonts.googleapis.com/css2?family=Open+Sans:wght@300;400&display=swap">
<style>
  :root {
    --page-bg: #e9e6e1;
    --blue-deep: #1768b4;
    --blue-main: #1f7dc4;
    --blue-mid: #3a9fd8;
    --blue-light: #a9dcf3;
    --white: #ffffff;
    --grey-soft: #f1f2f4;
    --logo-grey: #9aa0a6;
    --logo-blue: #8fd0f0;
  }
  * { margin: 0; padding: 0; box-sizing: border-box; }
  html, body { width: 1200px; height: 1136px; overflow: hidden; }
  body {
    background: var(--page-bg);
    font-family: "Open Sans", Arial, sans-serif;
    display: flex;
    flex-direction: column;
    align-items: center;
    justify-content: space-evenly;
  }
  .card {
    position: relative;
    width: 900px;
    height: 514px;
    border-radius: 6px;
    overflow: hidden;
    background: linear-gradient(160deg, var(--blue-main) 0%, var(--blue-deep) 100%);
    box-shadow: 0 10px 26px rgba(0,0,0,0.18);
    color: var(--white);
  }
  .card__arc { position: absolute; inset: 0; }

  /* wordmark */
  .wordmark { display: flex; align-items: center; gap: 22px; position: absolute; }
  .wordmark__dot {
    width: 96px; height: 96px; border-radius: 50%;
    border: 3px solid currentColor;
  }
  .wordmark__text {
    font-weight: 300;
    text-transform: uppercase;
    line-height: 1.05;
  }
  .wordmark__name { display: block; font-size: 64px; letter-spacing: 6px; }
  .wordmark__tag { display: block; font-size: 26px; letter-spacing: 3px; }

  /* front */
  .card--front .wordmark { top: 70px; left: 330px; color: var(--logo-grey); }
  .contact {
    position: absolute; left: 70px; bottom: 52px;
  }
  .contact__name { font-size: 30px; font-weight: 400; }
  .contact__post { font-size: 14px; font-weight: 300; color: var(--blue-light); letter-spacing: 1px; margin-bottom: 12px; }
  .contact__cred { font-size: 18px; font-weight: 300; line-height: 1.35; margin-bottom: 20px; }
  .contact__list { list-style: none; font-size: 19px; font-weight: 300; }
  .contact__list li { display: flex; align-items: center; gap: 14px; line-height: 1.65; }
  .contact__list svg { width: 18px; height: 18px; fill: var(--white); opacity: 0.85; }

  /* back */
  .card--back .wordmark { top: 92px; left: 190px; color: var(--white); }
  .card--back .wordmark__dot { width: 150px; height: 150px; }
  .card--back .wordmark__name { font-size: 84px; }
  .card--back .wordmark__tag { font-size: 32px; }
  .services {
    position: absolute; top: 300px; left: 0; right: 0;
    text-align: center; font-size: 23px; font-weight: 300; line-height: 1.55;
  }
  .services__pill {
    display: inline-block; margin-top: 22px;
    padding: 8px 40px; border-radius: 30px;
    background: var(--blue-light); color: var(--blue-deep);
    font-size: 24px; font-weight: 400;
  }
</style>
</head>
<body>

  <section class="card card--front" aria-label="Business card front">
    <svg class="card__arc" viewBox="0 0 900 514" preserveAspectRatio="none" aria-hidden="true">
      <defs>
        <linearGradient id="whiteFade" x1="0" y1="0" x2="1" y2="1">
          <stop offset="0" stop-color="#ffffff"/>
          <stop offset="1" stop-color="#eceef1"/>
        </linearGradient>
      </defs>
      <ellipse cx="600" cy="-60" rx="520" ry="345" fill="#3a9fd8"/>
      <ellipse cx="600" cy="-60" rx="505" ry="330" fill="#a9dcf3"/>
      <ellipse cx="600" cy="-60" rx="492" ry="315" fill="url(#whiteFade)"/>
    </svg>
    <div class="wordmark">
      <span class="wordmark__dot"></span>
      <span class="wordmark__text">
        <span class="wordmark__name">Moravel</span>
        <span class="wordmark__tag">Aesthetic Doctor</span>
      </span>
    </div>
    <div class="contact">
      <p class="contact__name">Dr Elena Varsk</p>
      <p class="contact__post">MRCPCH MD</p>
      <p class="contact__cred">Australasian Diploma of<br>Aesthetic Medicine</p>
      <ul class="contact__list">
        <li><svg viewBox="0 0 24 24"><path d="M6.6 10.8a15 15 0 0 0 6.6 6.6l2.2-2.2a1 1 0 0 1 1-.25 11.4 11.4 0 0 0 3.6.57 1 1 0 0 1 1 1V20a1 1 0 0 1-1 1A17 17 0 0 1 3 4a1 1 0 0 1 1-1h3.5a1 1 0 0 1 1 1c0 1.25.2 2.45.57 3.6a1 1 0 0 1-.25 1z"/></svg>0800 555 018</li>
        <li><svg viewBox="0 0 24 24"><path d="M2 5h20v14H2z M4 7v.4l8 5.2 8-5.2V7z" fill-rule="evenodd"/></svg>elena@moravel.co.nz</li>
        <li><svg viewBox="0 0 24 24"><circle cx="12" cy="12" r="10" fill="none" stroke="#fff" stroke-width="2"/><path d="M2 12h20M12 2c3 3 3 17 0 20M12 2c-3 3-3 17 0 20" fill="none" stroke="#fff" stroke-width="1.6"/></svg>www.moravel.co.nz</li>
      </ul>
    </div>
  </section>

  <section class="card card--back" aria-label="Business card back">
    <div class="wordmark">
      <span class="wordmark__dot"></span>
      <span class="wordmark__text">
        <span class="wordmark__name">Moravel</span>
        <span class="wordmark__tag">Aesthetic Doctor</span>
      </span>
    </div>
    <div class="services">
      <p>Dermal injectables - Plasma facials - Microneedling</p>
      <p>Skin boosters - Excessive sweating</p>
      <p class="services__pill">Home and Spa Based Treatments</p>
    </div>
  </section>

</body>
</html>
```